Responsive web design for leading product search engine

Findnearby is the leading product search engine in Australia and is soon to expand into Asia. We need a lightweight responsive homepage designed for our 3 regional domains. Our domains are Findnearby.com, Findnearby.com.au and Findnearby.asia. We need 3 versions of the same page to appeal to each region. The page and images used need to use a responsive html 5 based web page. The images used in the design need to be responsive and include CSS3 style elements.

For inspiration I would divert you to www.brovanta.com and www.pelmiqo.com.au and I have attached a mockup of what I think it could look like.
Updates

Target Market(s)

Target market is female shoppers 16-40 years old

Industry/Entity Type

Retail

Coding

Coded - Design and coding required

Number of Pages Required

3 page

Colors
33b8a4

Requirements
Must have
• Different image for each of the 3 duplicate pages. 1 for each region Australia (.com.au) Asia (.asia) US (.com). These images must be licensed for public use.

```html
<!DOCTYPE html>
<html lang="en">
<head>
<meta charset="UTF-8">
<title>Findnearby – Search products on sale at nearby stores</title>
<link rel="stylesheet" href="https://fonts.googleapis.com/css2?family=Open+Sans:wght@400;600;700&display=swap">
<style>
  :root {
    --teal: #33b8a4;
    --teal-dark: #2a9e8c;
    --ink: #3a3a3a;
    --muted: #8a8a8a;
    --white: #ffffff;
    --light: #f4f4f4;
    --hero-a: #b9a48c;
    --hero-b: #6f5a4a;
    --clients-a: #4d4f52;
    --clients-b: #8b8680;
  }
  * { box-sizing: border-box; margin: 0; padding: 0; }
  html, body { width: 1200px; height: 2340px; overflow: hidden; }
  body { font-family: "Open Sans", Arial, sans-serif; color: var(--ink); background: var(--white); position: relative; }

  /* Hero */
  .hero { position: absolute; top: 0; left: 0; width: 1200px; height: 660px; overflow: hidden; }
  .hero-photo { position: absolute; inset: 0; background: linear-gradient(120deg, var(--hero-a) 0%, #a7896f 40%, var(--hero-b) 100%); }
  .hero-shade { position: absolute; inset: 0; background: rgba(30, 25, 20, 0.28); }
  .site-header { position: absolute; top: 32px; left: 50px; right: 50px; display: flex; justify-content: space-between; align-items: center; }
  .brand { display: flex; align-items: center; gap: 12px; color: var(--white); font-weight: 700; font-size: 34px; }
  .brand-dot { width: 30px; height: 30px; border-radius: 50%; background: var(--teal); }
  .header-icons { display: flex; gap: 24px; align-items: center; }
  .hero-title { position: absolute; top: 230px; left: 0; width: 100%; text-align: center; color: var(--white); font-size: 46px; font-weight: 400; line-height: 1.2; }
  .search-bar { position: absolute; top: 392px; left: 330px; display: flex; gap: 6px; }
  .search-field { height: 40px; background: var(--white); border-radius: 2px; font-size: 12px; color: var(--muted); display: flex; align-items: center; padding: 0 16px; }
  .search-field.product { width: 220px; }
  .search-field.location { width: 210px; }
  .search-button { width: 100px; height: 40px; background: var(--teal); color: var(--white); font-size: 12px; font-weight: 600; display: flex; align-items: center; justify-content: center; border-radius: 2px; }
  .scroll-cue { position: absolute; top: 538px; left: 572px; }

  /* Discover */
  .discover { position: absolute; top: 660px; left: 0; width: 1200px; height: 400px; }
  .discover-device { position: absolute; top: 90px; left: 110px; width: 460px; height: 220px; border-radius: 36px; background: linear-gradient(135deg, #e9e9e9, #bdbdbd); transform: rotate(-8deg); }
  .discover-text { position: absolute; top: 80px; left: 695px; width: 400px; }
  .discover-text h2 { font-size: 34px; font-weight: 400; line-height: 1.25; color: var(--ink); margin-bottom: 22px; }
  .discover-text p { font-size: 13px; line-height: 1.6; color: var(--muted); }

  /* Services */
  .services { position: absolute; top: 1060px; left: 0; width: 1200px; height: 470px; background: var(--white); border-top: 1px solid #eee; }
  .services h2 { position: absolute; top: 110px; width: 100%; text-align: center; font-size: 34px; font-weight: 400; color: var(--ink); }
  .service { position: absolute; top: 185px; width: 220px; text-align: center; }
  .service-icon { width: 100px; height: 100px; border-radius: 50%; background: var(--teal); margin: 0 auto 26px; display: flex; align-items: center; justify-content: center; }
  .service h3 { font-size: 14px; font-weight: 700; color: var(--ink); margin-bottom: 10px; }
  .service p { font-size: 12px; line-height: 1.6; color: var(--muted); }

  /* Clients */
  .clients { position: absolute; top: 1530px; left: 0; width: 1200px; height: 445px; overflow: hidden; }
  .clients-photo { position: absolute; inset: 0; background: linear-gradient(90deg, var(--clients-a) 0%, #5e5d5c 50%, var(--clients-b) 100%); }
  .clients h2 { position: absolute; top: 90px; left: 100px; color: var(--white); font-size: 36px; font-weight: 400; }
  .quote { position: absolute; top: 180px; left: 100px; width: 440px; color: var(--white); font-size: 13px; line-height: 1.6; padding-left: 34px; }
  .quote::before { content: "\201C"; position: absolute; left: 0; top: -14px; font-size: 52px; line-height: 1; }
  .quote::after { content: "\201D"; position: absolute; right: -24px; bottom: -32px; font-size: 52px; line-height: 1; }
  .client { position: absolute; top: 310px; left: 100px; display: flex; align-items: center; gap: 16px; }
  .client-avatar { width: 70px; height: 70px; border-radius: 50%; background: #c9b3a3; border: 3px solid var(--white); }
  .client-name { font-size: 13px; font-weight: 600; color: var(--teal); }
  .client-role { font-size: 11px; color: #ddd; }
  .play { position: absolute; top: 140px; left: 810px; }

  /* Footer */
  .site-footer { position: absolute; top: 1975px; left: 0; width: 1200px; height: 365px; background: var(--teal); color: var(--white); text-align: center; }
  .footer-brand { position: absolute; top: 50px; left: 0; width: 100%; display: flex; justify-content: center; align-items: center; gap: 12px; font-size: 40px; font-weight: 700; }
  .footer-brand .brand-dot { background: var(--white); width: 34px; height: 34px; }
  .footer-links { position: absolute; top: 186px; width: 100%; display: flex; justify-content: center; gap: 30px; font-size: 12px; }
  .footer-note { position: absolute; top: 230px; width: 100%; font-size: 11px; line-height: 1.7; opacity: 0.9; }
  .store-badges { position: absolute; top: 296px; width: 100%; display: flex; justify-content: center; gap: 12px; }
  .store-badge { width: 96px; height: 30px; border-radius: 5px; background: #1e1e1e; }
  .footer-legal { position: absolute; top: 336px; width: 100%; display: flex; justify-content: center; gap: 30px; font-size: 10px; }
</style>
</head>
<body>

<section class="hero">
  <div class="hero-photo" role="img" aria-label="Two young women laughing together while shopping, holding bags in a city street"></div>
  <div class="hero-shade"></div>
  <header class="site-header">
    <div class="brand"><span class="brand-dot"></span>Findnearby</div>
    <div class="header-icons">
      <svg width="18" height="20" viewBox="0 0 18 20" aria-label="Account"><rect x="2" y="9" width="14" height="10" rx="1" fill="#fff"/><path d="M5 9V6a4 4 0 0 1 8 0v3" stroke="#fff" stroke-width="2" fill="none"/></svg>
      <svg width="22" height="18" viewBox="0 0 22 18" aria-label="Menu"><rect y="1" width="22" height="3" fill="#fff"/><rect y="8" width="22" height="3" fill="#fff"/><rect y="15" width="22" height="3" fill="#fff"/></svg>
    </div>
  </header>
  <h1 class="hero-title">Search millions of products on sale<br>at nearby stores</h1>
  <div class="search-bar">
    <div class="search-field product">Search business or product</div>
    <div class="search-field location">Current location</div>
    <div class="search-button">BOOK NOW</div>
  </div>
  <svg class="scroll-cue" width="56" height="56" viewBox="0 0 56 56" aria-label="Scroll down"><circle cx="28" cy="28" r="26" stroke="#fff" stroke-width="2" fill="none"/><path d="M18 24l10 10 10-10" stroke="#fff" stroke-width="2.5" fill="none"/></svg>
</section>

<section class="discover">
  <div class="discover-device" role="img" aria-label="Smartphone lying flat showing the Findnearby app with product listings"></div>
  <div class="discover-text">
    <h2>Discover the best products while you shop</h2>
    <p>Search sale products in stores near you and compare prices from local shops before you head out today.</p>
  </div>
</section>

<section class="services">
  <h2>Our services</h2>
  <div class="service" style="left:200px">
    <div class="service-icon"><svg width="36" height="32" viewBox="0 0 36 32"><path d="M2 3h6l4 18h18l4-13H10" stroke="#fff" stroke-width="3" fill="none"/><circle cx="14" cy="27" r="3" fill="#fff"/><circle cx="27" cy="27" r="3" fill="#fff"/></svg></div>
    <h3>TOP PRODUCTS</h3>
    <p>Browse the most wanted items from stores close by, updated every day for you.</p>
  </div>
  <div class="service" style="left:490px">
    <div class="service-icon"><svg width="38" height="30" viewBox="0 0 38 30"><path d="M2 14l8-8 9 6 9-6 8 8-9 10-8-6-8 6z" fill="#fff"/></svg></div>
    <h3>TOP DEAL</h3>
    <p>See the biggest price drops at nearby shops and grab them before they are gone.</p>
  </div>
  <div class="service" style="left:780px">
    <div class="service-icon"><svg width="36" height="36" viewBox="0 0 36 36"><circle cx="14" cy="20" r="9" stroke="#fff" stroke-width="4" fill="none"/><circle cx="27" cy="9" r="5" stroke="#fff" stroke-width="3" fill="none"/></svg></div>
    <h3>TOP BUSINESS</h3>
    <p>Find the best rated local stores near you, picked by shoppers in your own area.</p>
  </div>
</section>

<section class="clients">
  <div class="clients-photo" role="img" aria-label="Smiling woman looking at her phone in a softly lit room"></div>
  <h2>Our happy clients</h2>
  <p class="quote">Findnearby helped me find the exact boots I wanted at a shop two streets away, and on sale too. I now check it before every trip to town, and it saves me time and money each week.</p>
  <div class="client">
    <div class="client-avatar" role="img" aria-label="Portrait of the reviewer"></div>
    <div>
      <div class="client-name">Mara Quell</div>
      <div class="client-role">Weekend Shopper</div>
    </div>
  </div>
  <svg class="play" width="120" height="120" viewBox="0 0 120 120" aria-label="Play video"><circle cx="60" cy="60" r="56" stroke="#fff" stroke-opacity="0.7" stroke-width="3" fill="none"/><path d="M48 40l32 20-32 20z" fill="#fff" fill-opacity="0.7"/></svg>
</section>

<footer class="site-footer">
  <div class="footer-brand"><span class="brand-dot"></span>Findnearby</div>
  <nav class="footer-links"><span>Visit Find Nearby</span><span>Add your store</span><span>Login</span></nav>
  <p class="footer-note">© 2024 Findnearby.com<br>All trademarks and product names belong to their owners.<br>Prices and stock are set by each local store.</p>
  <div class="store-badges"><span class="store-badge"></span><span class="store-badge"></span></div>
  <div class="footer-legal"><span>Terms of Use</span><span>Privacy</span></div>
</footer>

</body>
</html>
```